Belvascotravel.com web design project + logo design

Hi,

We are a Russian online tour operator - sunkettle.com

We are looking to tranmsfer our domain to belvascotravel.com. The website and logo need to be belvascoesque - we are not looking to change our functionality, but we need to make the website much more attracitve to clients, much more wild looking but at the same time remaining a professional travel company.

The main concept of the website should be innovative travel (as belvasco was an innovator). Alternatively, you could go down the artist route and go down the draw / design your own tour road.

On our website the customer is able to combine travel services (hotels, flights, Visa services, and soon chauffeur, car rental etc...) put it into their basket (the basket definitely has to look better than it is at the moment) and pay for it in one go by card.

We are also stressin our customer support with web chat, call centre etc... (call centre number at the top of the page)

We aim to provide an easy user experience, but we need to make it have some more style, so I will be waiting for what you guys can come up with.
Let me know if you have any questions - skype is: mrdolbarin

Industry/Entity Type

It Company

Requirements
Must have
• It is quite a simple task - to take the existing website sunkettle.com and belvascosize it to create belvascotravel.com, the functionality of the website will remain the same and there are not many pages in the website. Homepage, Checkout step1, Checkout step 2 (you can view both of these if you select a service) and the generic pages for T&C''s, Privacy policy etc...

IMPORTANT UPDATE

We are also looking at how the search results will look in the designs, (please do a search on our website for hotel / flight)

```html
<!DOCTYPE html>
<html lang="ru">
<head>
<meta charset="utf-8">
<title>Sunkettle — Связаться</title>
<link rel="stylesheet" href="https://fonts.googleapis.com/css2?family=Ubuntu:wght@400;500;700&family=PT+Sans:wght@400;700&display=swap">
<style>
  :root {
    --header-dark: #120b06;
    --header-brown: #3a2613;
    --gold: #c9a32a;
    --gold-text: #d9a640;
    --parchment: #d9c29a;
    --parchment-deep: #b99868;
    --blue: #5a78c0;
    --blue-tab: #4c6cbd;
    --field: #c4c7cc;
    --field-border: #8b8e93;
    --button: #2e1a08;
    --ink: #1d1d1d;
    --white: #ffffff;
    --button-grey: #8d8f92;
    --call-label: #7d9be0;
  }
  * { box-sizing: border-box; margin: 0; padding: 0; }
  html, body { width: 1123px; height: 1200px; overflow: hidden; background: var(--white); }
  body { position: relative; font-family: "PT Sans", Arial, sans-serif; color: var(--ink); }

  .parchment-band {
    position: absolute; left: 0; top: 150px; width: 1123px; height: 200px;
    background: linear-gradient(180deg, var(--parchment-deep) 0%, var(--parchment) 45%, #efe3cb 80%, var(--white) 100%);
  }
  .sketch-figure {
    position: absolute; left: 0; top: 150px; width: 300px; height: 480px;
    background: radial-gradient(ellipse at 30% 40%, rgba(150,120,80,.25), rgba(255,255,255,0) 70%);
  }
  .header-shelf {
    position: absolute; left: 680px; top: 120px; width: 443px; height: 100px;
    background: #050302; border-bottom-left-radius: 40px; z-index: 1;
  }
  .site-header {
    position: absolute; left: 0; top: 0; width: 1123px; height: 160px; z-index: 2;
    background: linear-gradient(90deg, #a38a1e 0%, #5a4212 14%, var(--header-brown) 30%, var(--header-dark) 60%, #000 100%);
  }
  .wing-art {
    position: absolute; left: 10px; top: 36px; width: 210px; height: 84px;
    background: linear-gradient(180deg, #d8cfae, #8d8466);
    border-radius: 50% 10% 50% 50%; opacity: .85;
  }
  .brand { position: absolute; left: 150px; top: 24px; display: flex; align-items: center; gap: 14px; }
  .brand-dot { width: 60px; height: 60px; border-radius: 50%; background: var(--gold); }
  .brand-name { font-family: "Ubuntu", sans-serif; font-size: 44px; font-weight: 500; color: var(--white); }

  .call-center {
    position: absolute; right: 400px; top: 40px; text-align: right;
    font-family: "Ubuntu", sans-serif; color: var(--white); white-space: nowrap;
  }
  .call-center .label { font-size: 25px; font-weight: 500; color: var(--call-label); line-height: 30px; }
  .call-center .main-phone { font-size: 28px; font-weight: 700; line-height: 32px; }
  .call-center .city-phone { font-size: 22px; line-height: 28px; }
  .operator-portrait {
    position: absolute; left: 736px; top: 54px; width: 44px; height: 76px; z-index: 3;
    border-radius: 0 38px 38px 0; background: linear-gradient(90deg, #1f3d8a, #b9c3d8);
  }
  .hours {
    position: absolute; left: 838px; top: 68px; width: 215px; text-align: center;
    font-family: "Ubuntu", sans-serif; font-size: 21px; line-height: 26px; color: var(--gold-text);
  }

  .top-nav { position: absolute; left: 735px; top: 0; display: flex; gap: 4px; z-index: 3; }
  .top-nav a {
    display: block; width: 118px; height: 26px; text-align: center; line-height: 26px;
    font-size: 17px; text-decoration: none;
  }
  .top-nav .home { background: var(--white); color: #000; border-bottom: 3px solid #7a7a7a; }
  .top-nav .contacts { background: #6d89d0; color: var(--white); }

  .tool-buttons { position: absolute; left: 735px; top: 155px; display: flex; gap: 4px; z-index: 3; }
  .tool-button {
    width: 118px; height: 64px; display: flex; align-items: center; justify-content: center;
    background: linear-gradient(180deg, #a7a9ac, var(--button-grey) 55%, #6e7073);
    border: 1px solid #5a5c5f;
  }

  .medallion {
    position: absolute; top: 300px; width: 94px; height: 94px; border-radius: 50%;
    border: 4px solid #e8dcc0; box-shadow: 2px 3px 6px rgba(0,0,0,.35);
  }
  .medallion.flight { left: 735px; background: radial-gradient(circle, #d4c79a, #8f7d4a); }
  .medallion.hotel { left: 842px; background: radial-gradient(circle, #dfc8b4, #9b7a62); }
  .medallion.visa { left: 949px; background: radial-gradient(circle, #e0cda6, #9c7b45); }

  .contact-tab {
    position: absolute; left: 146px; top: 374px; width: 210px; height: 58px;
    background: var(--blue-tab); border-radius: 18px 18px 0 0;
    color: var(--white); font-size: 22px; font-weight: 700; padding: 12px 22px;
  }
  .contact-card {
    position: absolute; left: 146px; top: 428px; width: 895px; height: 412px;
    background: var(--blue); border-radius: 0 26px 26px 26px;
  }
  .contact-form {
    position: absolute; left: 9px; top: 9px; width: 625px; height: 394px;
    background: var(--white); border-radius: 0 26px 26px 22px;
  }
  .form-label { position: absolute; left: 16px; font-size: 15px; }
  .field { position: absolute; left: 78px; background: var(--field); border: 2px solid var(--field-border); }
  .field.name { top: 48px; width: 263px; height: 30px; }
  .field.email { top: 95px; width: 525px; height: 30px; }
  .field.subject { top: 143px; width: 525px; height: 192px; }
  .submit {
    position: absolute; left: 479px; top: 345px; width: 124px; height: 32px;
    background: var(--button); color: var(--white); border-radius: 16px;
    font-size: 16px; font-weight: 700; text-align: center; line-height: 32px;
  }
  .office-info { position: absolute; left: 640px; top: 0; width: 255px; height: 412px; color: var(--white); font-size: 15px; }
  .office-intro { position: absolute; left: 0; top: 20px; line-height: 19px; }
  .info-row { position: absolute; left: 0; display: flex; align-items: center; gap: 12px; line-height: 17px; }
</style>
</head>
<body>
  <div class="parchment-band" role="img" aria-label="Parchment texture with sketched codex drawings"></div>
  <div class="sketch-figure" role="img" aria-label="Faint sketch of human proportion study"></div>

  <div class="header-shelf"></div>
  <header class="site-header">
    <div class="wing-art" role="img" aria-label="Sketched feathered wing"></div>
    <div class="brand"><span class="brand-dot"></span><span class="brand-name">Sunkettle</span></div>
    <div class="call-center">
      <div class="label">Call Center</div>
      <div class="main-phone">8-800-555-0142</div>
      <div class="city-phone">+7 (495) 000-12-34</div>
    </div>
    <div class="hours">(Пн–Пт) Часы работы:<br>с 9:00 – до 18:00</div>
  </header>
  <div class="operator-portrait" role="img" aria-label="Support operator portrait"></div>

  <nav class="top-nav">
    <a class="home" href="#">Home</a>
    <a class="contacts" href="#">Contacs</a>
  </nav>

  <div class="tool-buttons">
    <div class="tool-button" aria-label="Web chat">
      <svg width="50" height="44" viewBox="0 0 50 44">
        <ellipse cx="20" cy="18" rx="18" ry="14" fill="#f2a93b"/>
        <ellipse cx="31" cy="26" rx="16" ry="12" fill="#4c7fd8"/>
        <path d="M38 34 L44 42 L30 36 Z" fill="#4c7fd8"/>
      </svg>
    </div>
    <div class="tool-button" aria-label="Русский язык">
      <svg width="46" height="32" viewBox="0 0 46 32">
        <rect width="46" height="11" fill="#ffffff"/>
        <rect y="11" width="46" height="10" fill="#1f4fb5"/>
        <rect y="21" width="46" height="11" fill="#d2262b"/>
      </svg>
    </div>
    <div class="tool-button" aria-label="Личный кабинет">
      <svg width="40" height="46" viewBox="0 0 40 46">
        <circle cx="20" cy="13" r="11" fill="#b8babd"/>
        <path d="M2 46 C2 28 38 28 38 46 Z" fill="#b8babd"/>
      </svg>
    </div>
  </div>

  <div class="medallion flight" role="img" aria-label="Medallion with sketched flying machine"></div>
  <div class="medallion hotel" role="img" aria-label="Medallion with sketched domed building"></div>
  <div class="medallion visa" role="img" aria-label="Medallion with sketched polyhedron"></div>

  <div class="contact-tab">Связаться</div>
  <section class="contact-card">
    <form class="contact-form">
      <span class="form-label" style="top:54px">Name</span>
      <div class="field name"></div>
      <span class="form-label" style="top:102px">email</span>
      <div class="field email"></div>
      <span class="form-label" style="top:148px">Subject</span>
      <div class="field subject"></div>
      <div class="submit">Submit</div>
    </form>
    <div class="office-info">
      <p class="office-intro">Если вам необходимо связаться<br>с сотрудниками компании –<br>пожалуйста заполните форму<br>слева.<br>Офис в Лондоне</p>
      <div class="info-row" style="top:142px">
        <svg width="40" height="40" viewBox="0 0 40 40"><path d="M20 2 L25 15 L39 15 L28 24 L32 38 L20 30 L8 38 L12 24 L1 15 L15 15 Z" fill="#3f8ee8" stroke="#d8e6ff" stroke-width="1.5"/></svg>
        <span>Sunkettle Limited<br>14 Harrow Lane<br>London, E2 7QX<br>United Kingdom</span>
      </div>
      <div class="info-row" style="top:238px">
        <svg width="40" height="42" viewBox="0 0 40 42"><path d="M10 3 C4 6 3 14 8 24 C14 35 22 40 29 39 L33 32 L25 26 L20 30 C16 27 13 21 13 16 L19 13 L17 3 Z" fill="#3f8ee8" stroke="#d8e6ff" stroke-width="1.5"/></svg>
        <span>+7 (495) 000-12-34</span>
      </div>
      <div class="info-row" style="top:297px">
        <svg width="50" height="36" viewBox="0 0 50 36"><rect x="1" y="1" width="48" height="34" rx="3" fill="#3f8ee8" stroke="#d8e6ff" stroke-width="1.5"/><path d="M2 3 L25 21 L48 3" fill="none" stroke="#d8e6ff" stroke-width="2"/></svg>
        <span>info@sunkettle.com</span>
      </div>
    </div>
  </section>
</body>
</html>
```